R. Talmont Realty, Inc business card (2 sided), letterhead (1 sided) & #10 envelope (1 sided)

business card of standard size utilizing the attached logo. Side one with logo, Owen Talmont (my name), President / Broker (title), 805-317-2684 (phone), www.rtalmontrealty.example (website), 1726 Harlow Avenue, Suite 4052 San Luis Obiso, CA 93628 (business address) owen.rtalmontrealty@mailbox.example (e-mail address),
Side two - Log

Letterhead and #10 envelope in the same theme
Updates

Project Deadline Extended
Reason: I think a 2 day deadline may be a bit ambitious on my part. I have extended the deadline to 4 days. Thanks!

Industry/Entity Type

Business

```html
<!DOCTYPE html>
<html lang="en">
<head>
<meta charset="utf-8">
<title>R. Talmont Realty, Inc — Business Card</title>
<link href="https://fonts.googleapis.com/css2?family=Noto+Serif:wght@400;700&family=Open+Sans:wght@400;600&display=swap" rel="stylesheet">
<style>
  :root {
    --backdrop: #e8e5e0;
    --card-white: #ffffff;
    --brand-blue: #1a6e98;
    --brand-blue-deep: #0b4e72;
    --brand-blue-light: #2a86b3;
    --edge-dark: #2b2b2b;
    --ink: #1f3a4d;
    --on-blue: #ffffff;
  }
  * { box-sizing: border-box; margin: 0; padding: 0; }
  html, body {
    width: 1200px; height: 1183px; overflow: hidden;
    background: var(--backdrop);
  }
  .canvas { position: relative; width: 1200px; height: 1183px; }

  .card {
    position: absolute; width: 900px; height: 512px; overflow: hidden;
    box-shadow: 0 6px 18px rgba(0,0,0,0.18);
  }

  /* Front */
  .card-front { left: 260px; top: 40px; background: var(--card-white); }
  .card-front .panel-shape { position: absolute; inset: 0; }
  .card-front .brand {
    position: absolute; left: 50px; top: 224px; width: 400px;
    display: flex; align-items: center; gap: 12px;
    font-family: "Noto Serif", serif; font-weight: 700;
    font-size: 30px; color: var(--ink); white-space: nowrap;
  }
  .brand-mark { width: 16px; height: 16px; background: var(--brand-blue); flex: none; }
  .contact {
    position: absolute; right: 36px; top: 100px; text-align: right;
    color: var(--on-blue);
  }
  .contact .name {
    font-family: "Noto Serif", serif; font-weight: 700; font-size: 32px; line-height: 1.2;
  }
  .contact .title {
    font-family: "Noto Serif", serif; font-weight: 400; font-size: 24px; margin-top: 2px;
  }
  .contact .lines {
    list-style: none; margin-top: 26px;
    font-family: "Open Sans", sans-serif; font-size: 16px; line-height: 36px;
  }
  .contact .lines li { display: flex; justify-content: flex-end; align-items: center; gap: 8px; white-space: nowrap; }
  .contact .lines svg { width: 16px; height: 16px; flex: none; }

  /* Back */
  .card-back {
    left: 50px; top: 620px;
    background: radial-gradient(ellipse at 50% 40%, var(--brand-blue-light) 0%, var(--brand-blue) 45%, var(--brand-blue-deep) 100%);
    color: var(--on-blue);
  }
  .card-back .brand {
    position: absolute; left: 0; right: 0; top: 200px;
    display: flex; justify-content: center; align-items: center; gap: 16px;
    font-family: "Noto Serif", serif; font-weight: 700; font-size: 46px; white-space: nowrap;
  }
  .card-back .brand-mark { width: 22px; height: 22px; background: var(--on-blue); }
  .card-back .website {
    position: absolute; left: 0; right: 0; top: 418px; text-align: center;
    font-family: "Open Sans", sans-serif; font-weight: 600; font-size: 25px; letter-spacing: 3px;
  }
</style>
</head>
<body>
<main class="canvas">

  <section class="card card-front" aria-label="Business card front">
    <svg class="panel-shape" viewBox="0 0 900 512" aria-hidden="true">
      <defs>
        <linearGradient id="panelFill" x1="0" y1="0" x2="1" y2="1">
          <stop offset="0" stop-color="#1f79a5"/>
          <stop offset="1" stop-color="#0c5279"/>
        </linearGradient>
      </defs>
      <polygon points="630,0 900,0 900,512 594,512 470,198" fill="none" stroke="var(--edge-dark)" stroke-width="5"/>
      <polygon points="644,0 900,0 900,512 608,512 486,198" fill="url(#panelFill)"/>
    </svg>

    <div class="brand"><span class="brand-mark"></span>R. Talmont Realty, Inc</div>

    <div class="contact">
      <p class="name">Owen Talmont</p>
      <p class="title">President / Broker</p>
      <ul class="lines">
        <li>
          <svg viewBox="0 0 24 24" aria-hidden="true"><path fill="#fff" d="M6.6 10.8a15 15 0 0 0 6.6 6.6l2.2-2.2c.3-.3.7-.4 1-.2 1.1.4 2.3.6 3.6.6.6 0 1 .4 1 1V20c0 .6-.4 1-1 1A17 17 0 0 1 3 4c0-.6.4-1 1-1h3.5c.6 0 1 .4 1 1 0 1.3.2 2.5.6 3.6.1.3 0 .7-.2 1z"/></svg>
          805-317-2684
        </li>
        <li>
          <svg viewBox="0 0 24 24" aria-hidden="true"><rect x="2" y="5" width="20" height="14" rx="2" fill="#fff"/><path d="M3 6l9 7 9-7" stroke="#1a6e98" stroke-width="2" fill="none"/></svg>
          owen.rtalmontrealty@mailbox.example
        </li>
        <li>
          <svg viewBox="0 0 24 24" aria-hidden="true"><g fill="none" stroke="#fff" stroke-width="2"><circle cx="12" cy="12" r="9"/><ellipse cx="12" cy="12" rx="4" ry="9"/><path d="M3 12h18"/></g></svg>
          www.rtalmontrealty.example
        </li>
      </ul>
    </div>
  </section>

  <section class="card card-back" aria-label="Business card back">
    <div class="brand"><span class="brand-mark"></span>R. Talmont Realty, Inc</div>
    <p class="website">www.rtalmontrealty.example</p>
  </section>

</main>
</body>
</html>
```